Harlow Advisory, Business Cards for International Development Consultancy

I'm an independent consultant working in the international development sector. I work with small organisations in developing countries to help them develop their community based programs so that they can be internationally competitive. This means they need to work better with their own communities to deliver meaningful quality work and also improve the accountability of their work so that they can compete for international and domestic funding.

I like the idea of being a connector between community, local organisations and international best practice and back again (ie acknowledging that international best practice can learn a lot from community).

My surname is Harlow - so I'd like the logo to use the idea of web as a connector.

I work with people with sight impairments - would like my card to be useful for low vision (i.e. clear graphics, easy to read font) and no vision (i.e. brail).

Target Market(s)

international non-government organisations (i.e. pelmark, lift the hamlets, kindred arc), Blue Shield Gold Lantern, government (i.e. Australian Bureau of Overseas Relations, consulars), non government agencies,

Industry/Entity Type

Business

Contact Information for Business Card

International Development Consultant
Bridging Global Practice and Local Community Voices

Marcia Harlow
Lead Consultant
Phone: +61 412 583720
Email: mharlow.advisory@postnest.example

Font styles to use
Sans Serif

Colors
eaf1f7
85acd3
d3a5cc
0456a4
a64599
0255a3

Requirements
Nice to have
• brail
Should not have
• fancy fonts - needs to be easy to read.

```html
<!DOCTYPE html>
<html lang="en">
<head>
<meta charset="utf-8">
<title>Harlow Advisory – Business Cards</title>
<link rel="stylesheet" href="https://fonts.googleapis.com/css2?family=Questrial&display=swap">
<style>
  :root {
    --backdrop: #e4e6ea;
    --card-white: #f3f3f1;
    --ink: #1b1b1d;
    --brand-blue: #0456a4;
    --brand-deep: #0255a3;
    --brand-light: #85acd3;
    --brand-pale: #eaf1f7;
    --silver: #c9ced6;
  }
  * { box-sizing: border-box; margin: 0; padding: 0; }
  html, body {
    width: 1200px; height: 968px; overflow: hidden;
    background: var(--backdrop);
    font-family: "Questrial", "Century Gothic", sans-serif;
  }
  .sheet {
    width: 1200px; height: 968px;
    display: flex; flex-direction: column; align-items: center; justify-content: center;
    gap: 48px;
  }
  .card {
    position: relative;
    width: 735px; height: 420px;
    border-radius: 34px;
    overflow: hidden;
    box-shadow: 0 6px 18px rgba(0,0,0,.18);
  }
  /* Front */
  .card--front { background: var(--card-white); color: var(--ink); }
  .front__band {
    position: absolute; top: 0; right: 0; width: 430px; height: 230px;
  }
  .front__identity { position: absolute; left: 50px; top: 92px; }
  .front__name { font-size: 38px; font-weight: 400; letter-spacing: .5px; line-height: 1; }
  .front__role { font-size: 20px; color: var(--brand-blue); margin-top: 6px; }
  .front__contacts { position: absolute; left: 52px; top: 182px; list-style: none; }
  .contact { display: flex; align-items: center; gap: 14px; font-size: 20px; margin-bottom: 14px; }
  .contact svg { width: 28px; height: 22px; flex: none; }
  .front__brand {
    position: absolute; left: 52px; top: 300px;
    display: flex; align-items: center; gap: 12px;
    font-size: 24px; color: var(--brand-blue);
  }
  .brand__square { width: 22px; height: 22px; background: var(--brand-blue); }
  .front__tagline {
    position: absolute; right: 44px; bottom: 34px;
    font-size: 22px; color: var(--ink);
  }
  /* Back */
  .card--back {
    background: linear-gradient(135deg, var(--brand-blue), #1f63b2 60%, var(--brand-deep));
    display: flex; flex-direction: column; align-items: center; justify-content: center; gap: 26px;
  }
  .back__square { width: 70px; height: 70px; background: var(--silver); opacity: .85; }
  .back__wordmark {
    font-size: 44px; letter-spacing: 10px; text-transform: uppercase;
    color: var(--silver);
  }
</style>
</head>
<body>
<main class="sheet">
  <section class="card card--front" aria-label="Business card front">
    <svg class="front__band" viewBox="0 0 430 230" role="img" aria-label="Decorative nested blue octagon stripes">
      <defs>
        <linearGradient id="bandFill" x1="0" y1="1" x2="1" y2="0">
          <stop offset="0" stop-color="#0456a4"/>
          <stop offset="1" stop-color="#85acd3"/>
        </linearGradient>
      </defs>
      <polygon points="0,0 430,0 430,215 350,230 170,210 60,120" fill="url(#bandFill)"/>
    </svg>

    <div class="front__identity">
      <h1 class="front__name">Marcia Harlow</h1>
      <p class="front__role">Lead Consultant</p>
    </div>

    <ul class="front__contacts">
      <li class="contact">
        <svg viewBox="0 0 28 22" aria-hidden="true">
          <rect x="1" y="2" width="26" height="18" rx="2" fill="#0456a4"/>
          <path d="M2 4 L14 13 L26 4" stroke="#eaf1f7" stroke-width="2" fill="none"/>
        </svg>
        <span>+61 412 583720</span>
      </li>
      <li class="contact">
        <svg viewBox="0 0 28 22" aria-hidden="true">
          <path d="M2 8 Q14 -2 26 8 L22 11 L19 7 L9 7 L6 11 Z" fill="#0456a4"/>
          <rect x="5" y="11" width="18" height="10" rx="2" fill="#0456a4"/>
          <circle cx="14" cy="16" r="2.5" fill="#eaf1f7"/>
        </svg>
        <span>mharlow.advisory@postnest.example</span>
      </li>
    </ul>

    <div class="front__brand">
      <span class="brand__square" aria-hidden="true"></span>
      <span>Harlow Advisory</span>
    </div>

    <p class="front__tagline">Bridging Global Practice and Local Community Voices</p>
  </section>

  <section class="card card--back" aria-label="Business card back">
    <span class="back__square" aria-hidden="true"></span>
    <p class="back__wordmark">Harlow Advisory</p>
  </section>
</main>
</body>
</html>
```